Quorva - corporate Business Card

We need a good look and innovative business card for a new start up company based in Los Angeles called "Quorva". We are in a payment business, including payment card, app, and ewallet. We are expert in online payment and Card not present (CNP) transaction.
We need an innovative, modern business card.

Our logo font is Aero Matics

Target Market(s)

Startup - Bank - Online Payment - Card Manufacturing

Industry/Entity Type

Startup

Contact Information for Business Card

phone: 555 014 7396 - Address: 4172 Marlowe blvd, Cylver City, CA 90299

Requirements
Must have
• Message: innovative, professional, expert, high tech, trust, online payment expert, security
Nice to have
• no comment
Should not have
• no Comment

```html
<!DOCTYPE html>
<html lang="en">
<head>
<meta charset="utf-8">
<title>Quorva – Business Card, Services Side</title>
<link rel="stylesheet" href="https://fonts.googleapis.com/css2?family=Exo+2:wght@500&family=Montserrat:wght@500&display=swap">
<style>
  :root {
    --canvas-bg: #e9e9e9;
    --card-red: #b11e2f;
    --card-ink: #ffffff;
    --rule: rgba(255, 255, 255, 0.9);
  }

  html, body {
    margin: 0;
    padding: 0;
    width: 1200px;
    height: 840px;
    overflow: hidden;
    background: var(--canvas-bg);
  }

  .stage {
    width: 1200px;
    height: 840px;
    display: flex;
    align-items: center;
    justify-content: center;
  }

  .business-card {
    position: relative;
    width: 700px;
    height: 400px;
    background: var(--card-red);
    color: var(--card-ink);
    box-shadow: 0 10px 30px rgba(0, 0, 0, 0.12);
  }

  .services-heading {
    position: absolute;
    left: 0;
    right: 0;
    top: 150px;
    display: flex;
    align-items: center;
    gap: 22px;
  }

  .heading-rule {
    flex: 1;
    height: 2px;
    background: var(--rule);
  }

  .heading-title {
    margin: 0;
    font-family: "Exo 2", sans-serif;
    font-weight: 500;
    font-size: 46px;
    letter-spacing: 0.5px;
    line-height: 1;
    white-space: nowrap;
  }

  .service-values {
    position: absolute;
    left: 0;
    right: 0;
    top: 240px;
    margin: 0;
    text-align: center;
    font-family: "Montserrat", sans-serif;
    font-weight: 500;
    font-size: 19px;
    line-height: 1.55;
    letter-spacing: 0.3px;
  }

  .service-values span {
    display: block;
  }
</style>
</head>
<body>
  <main class="stage">
    <article class="business-card" aria-label="Quorva business card, services side">
      <header class="services-heading">
        <span class="heading-rule"></span>
        <h1 class="heading-title">Our Services</h1>
        <span class="heading-rule"></span>
      </header>
      <p class="service-values">
        <span>Innovative | Professional | Expert | High Tech</span>
        <span>Trust | Online Payment Expert | Security</span>
      </p>
    </article>
  </main>
</body>
</html>
```